American cannabis tech company business card design

Pavrel.com is seeking a modern, professional, and brand-aligned business card that represents our company and its core values: Mission, Story, Values, and Impact. As an innovative cannabis company, we want a business card that is not only visually appealing but also serves as a representation of who we are and what we stand for.

Project Scope: Design a double-sided business card that integrates our brand identity and core values. Incorporate our key brand elements, ensuring a sleek and contemporary aesthetic. Visually reflect our core values (Mission, Story, Values, Impact) in a way that is engaging yet professional.

Target Market(s)

Vendors, third parties,

Contact Information for Business Card

Contact details (name, title, email, phone, website, etc.)

Font styles to use
Other font styles liked:
• Caslon, Centra

Colors

Designer to choose colors to be used in the design.

Requirements
Must have
• Pavrel.com logo and branding A creative yet clean way to integrate our core values (Mission, Story, Values, Impact) Modern typography and a well-structured layout
Nice to have
• forest green, grey, white, black
Should not have
• references to marijuana, leafs, plants, or related product

```html
<!DOCTYPE html>
<html lang="en">
<head>
<meta charset="UTF-8">
<title>Pavrel Business Card</title>
<link href="https://fonts.googleapis.com/css2?family=Playfair+Display:wght@700;900&family=Montserrat:wght@400;500&display=swap" rel="stylesheet">
<style>
  :root {
    --forest: #1b3320;
    --cream: #fbf9f3;
    --white: #ffffff;
    --ink: #1b3320;
    --backdrop: #2e2e2e;
  }
  * { margin: 0; padding: 0; box-sizing: border-box; }
  html, body { width: 1200px; height: 875px; overflow: hidden; }
  body {
    background: var(--backdrop);
    position: relative;
    font-family: "Montserrat", sans-serif;
  }
  .card {
    position: absolute;
    width: 540px;
    height: 310px;
    border-radius: 22px;
    overflow: hidden;
    box-shadow: 0 18px 40px rgba(0,0,0,0.45);
  }
  .card-front {
    left: 50px;
    top: 130px;
    background: var(--forest);
    display: flex;
    align-items: center;
    justify-content: center;
  }
  .front-wordmark {
    font-family: "Playfair Display", serif;
    font-weight: 900;
    font-size: 104px;
    letter-spacing: 1px;
    color: var(--cream);
  }
  .card-back {
    left: 610px;
    top: 435px;
    background: var(--white);
  }
  .back-wordmark {
    position: absolute;
    left: 38px;
    top: 104px;
    font-family: "Playfair Display", serif;
    font-weight: 900;
    font-size: 42px;
    color: var(--forest);
  }
  .divider {
    position: absolute;
    left: 228px;
    top: 70px;
    width: 1px;
    height: 120px;
    background: var(--ink);
  }
  .contact {
    position: absolute;
    left: 244px;
    top: 66px;
    color: var(--ink);
  }
  .contact-name {
    font-family: "Playfair Display", serif;
    font-weight: 700;
    font-size: 21px;
    line-height: 1.1;
  }
  .contact-title {
    font-family: "Playfair Display", serif;
    font-weight: 700;
    font-size: 11px;
    margin: 2px 0 8px 18px;
  }
  .contact-line {
    display: flex;
    align-items: center;
    gap: 7px;
    font-size: 14px;
    line-height: 1.55;
    margin-left: 8px;
  }
  .contact-line svg { width: 11px; height: 11px; fill: var(--ink); flex: none; }
  .address-band {
    position: absolute;
    left: 0;
    right: 0;
    top: 236px;
    height: 32px;
    background: var(--forest);
    color: var(--white);
    font-size: 13px;
    letter-spacing: 0.3px;
    display: flex;
    align-items: center;
    justify-content: center;
  }
</style>
</head>
<body>
  <section class="card card-front">
    <div class="front-wordmark">PAVREL</div>
  </section>

  <section class="card card-back">
    <div class="back-wordmark">PAVREL</div>
    <div class="divider"></div>
    <div class="contact">
      <div class="contact-name">Daniel Hartley</div>
      <div class="contact-title">Owner</div>
      <div class="contact-line">
        <svg viewBox="0 0 24 24"><path d="M6.6 10.8a15.1 15.1 0 0 0 6.6 6.6l2.2-2.2a1 1 0 0 1 1-.25 11.4 11.4 0 0 0 3.6.57 1 1 0 0 1 1 1V20a1 1 0 0 1-1 1A17 17 0 0 1 3 4a1 1 0 0 1 1-1h3.5a1 1 0 0 1 1 1c0 1.25.2 2.45.57 3.6a1 1 0 0 1-.25 1z"/></svg>
        <span>555-014-2288</span>
      </div>
      <div class="contact-line">
        <svg viewBox="0 0 24 24"><path d="M2 5h20v14H2zm2 2v.5l8 5 8-5V7z"/></svg>
        <span>info@pavrel.com</span>
      </div>
      <div class="contact-line">
        <svg viewBox="0 0 24 24"><circle cx="12" cy="12" r="10"/></svg>
        <span>www.pavrel.com</span>
      </div>
    </div>
    <div class="address-band">418 Larkin Ave, #112 Brookfield, OH 430417</div>
  </section>
</body>
</html>
```